New Innovative Counselling and psychotherapy Service needs Business Card design

Keep it simple and professional. On one side, just company name and logo (perhaps in all blue) and maybe a tag line.

On other side (all white) my name and Qualifications in centre

Industry/Entity Type

Health And Wellness

Contact Information for Business Card

Dara Whelby
Counsellor & Psychotherapist
BSc (Psychol.), BA, Dip. (Couns. & Psych.), PG.Cert (CBT), FGTrK, ONRE

I will also require Mobile no, Email and web site address of which I'll pass on to final designer.

Font styles to use
Sans Serif

Requirements
Must have
• My Logo Only and please use the colours in logo that is in it.
Should not have
• Any other images

```html
<!DOCTYPE html>
<html lang="en">
<head>
<meta charset="utf-8">
<title>Thrive Lane – Business Card</title>
<link rel="stylesheet" href="https://fonts.googleapis.com/css2?family=Arimo:wght@400;700&display=swap">
<style>
  :root {
    --bg: #2b2b2b;
    --card-top: #ffffff;
    --card-bottom: #e4e4e4;
    --sky: #45b1e8;
    --ink: #2a2a2a;
    --ink-soft: #555555;
    --leaf: #7cc243;
  }
  * { margin: 0; padding: 0; box-sizing: border-box; }
  html, body {
    width: 1200px; height: 997px; overflow: hidden;
    background: var(--bg);
    font-family: "Arimo", Arial, sans-serif;
  }
  .stage {
    width: 1200px; height: 997px;
    display: flex; flex-direction: column;
    align-items: center; justify-content: center; gap: 64px;
  }
  .card {
    position: relative;
    width: 640px; height: 366px;
    border-radius: 24px;
    overflow: hidden;
    background: linear-gradient(160deg, var(--card-top) 30%, var(--card-bottom) 100%);
    box-shadow: 0 14px 30px rgba(0,0,0,0.45);
  }
  .card__swoosh { position: absolute; inset: 0; width: 100%; height: 100%; }
  .card__swoosh .band { fill: var(--sky); }
  .card__swoosh .rule { fill: var(--ink); }

  .mark {
    position: absolute;
    border-radius: 50%;
    background: var(--sky);
  }

  /* Name side */
  .card--person .mark { width: 58px; height: 58px; left: 48px; top: 226px; }
  .person {
    position: absolute; left: 130px; top: 196px;
    text-transform: uppercase;
  }
  .person__name {
    font-weight: 700; font-size: 40px; letter-spacing: 1px;
    color: var(--sky); line-height: 1;
  }
  .person__role {
    margin-top: 6px;
    font-size: 15px; color: var(--ink-soft); letter-spacing: 0.5px;
  }
  .person__quals {
    margin-top: 6px;
    font-size: 15px; color: var(--sky); line-height: 1.3; letter-spacing: 0.3px;
  }

  /* Brand side */
  .card--brand .mark { width: 96px; height: 96px; left: 64px; top: 196px; }
  .brand { position: absolute; left: 190px; top: 204px; }
  .brand__name {
    font-weight: 400; font-size: 52px; color: var(--ink);
    letter-spacing: 0.5px; line-height: 1;
  }
  .brand__tagline {
    margin-top: 10px; margin-left: 70px;
    font-size: 18px; color: var(--sky);
    text-transform: uppercase; letter-spacing: 1px;
  }
</style>
</head>
<body>
<main class="stage">

  <section class="card card--person" aria-label="Card front: practitioner details">
    <svg class="card__swoosh" viewBox="0 0 640 366" preserveAspectRatio="none" aria-hidden="true">
      <path class="band" d="M0,0 H640 V140 C470,72 250,46 0,78 Z"/>
      <path class="rule" d="M0,96 C250,62 470,88 640,154 V164 C470,100 250,74 0,102 Z"/>
    </svg>
    <span class="mark" aria-hidden="true"></span>
    <div class="person">
      <h1 class="person__name">Dara Whelby</h1>
      <p class="person__role">Counsellor &amp; Psychotherapist</p>
      <p class="person__quals">BSc (Psychol.), BA, Dip. (Couns. &amp; Psych.),<br>PG.Cert (CBT), FGTrK, ONRE</p>
    </div>
  </section>

  <section class="card card--brand" aria-label="Card back: practice name">
    <svg class="card__swoosh" viewBox="0 0 640 366" preserveAspectRatio="none" aria-hidden="true">
      <path class="band" d="M0,0 H640 V140 C470,72 250,46 0,78 Z"/>
      <path class="rule" d="M0,96 C250,62 470,88 640,154 V164 C470,100 250,74 0,102 Z"/>
    </svg>
    <span class="mark" aria-hidden="true"></span>
    <div class="brand">
      <h2 class="brand__name">Thrive Lane</h2>
      <p class="brand__tagline">A Place to Thrive</p>
    </div>
  </section>

</main>
</body>
</html>
```